Design website for new email startup

We are starting a company called Pingo.QZ (it will live at http://pingo.qz).

We would like the main landing page for our site designed. We have provided a very simple wireframe to help provide direction for the content it should include, but we do not expect the designers to adhere to it at all - we encourage unique ideas. There is some sample text in the wireframe - this does not have to be used, but may provide ideas.

We provide an easy way for people to manage email for a custom domain name. For example if you own "yourhouseword.example" you can point your DNS records to us and we'll make it easy to have emails addressed to your domain get forwarded to your existing email (gmail, etc). Folks running blogs, and other small sites can quickly setup email addresses for their domains and manage them in one place.

(For technical folks, we have you point your dns mx records to us, hence the name. That way all your email hits us and we can redirect it wherever you want. We make it easy to manage a single domain or a bunch of domains. Many domain registrars offer this service for a fee, and have clumsy management tools. We provide a robust simple toolset for free, as well as premium options).

The goal of the landing page is to get folks into the signup flow. The second priority flow is to have them take a look at the premium plan offerings.

We may offer the winning designer additional work for the remainder of the site design.
Updates

I've changed this project to a committed payment.  It is no longer refundable.  Thank you.

Target Market(s)

Bloggers, podcasters, designers, app developers - people who are a little tech savvy.

Industry/Entity Type

It Company

Font styles to use
Sans Serif

Colors

Designer to choose colors to be used in the design.

Requirements
Must have
• A full fidelity mockup (comp) of the landing page including the source file (psd, ai, etc).

Some sort of logo treatment for the pingo.qz brand

A call to action for signup, such as the suggested 'Get Started Here'
Nice to have
• A hip startup feel

Incorporation of the email theme

Give the impression it is simple, easy and fast

```html
<!DOCTYPE html>
<html lang="en">
<head>
<meta charset="utf-8">
<title>Pingo.QZ — Email for your domain</title>
<link href="https://fonts.googleapis.com/css2?family=Open+Sans:wght@400;600&display=swap" rel="stylesheet">
<style>
  :root {
    --olive: #7d8f22;
    --olive-btn: #8a9a2f;
    --olive-dark: #5e6e12;
    --ink: #111111;
    --text: #2b2b2b;
    --muted: #333333;
    --bar: #3a3a3a;
    --white: #ffffff;
    --card-grey: #efefef;
    --arrow-light: #8fd14a;
    --arrow-dark: #4f9a1c;
  }
  * { box-sizing: border-box; margin: 0; padding: 0; }
  html, body { width: 1200px; height: 836px; overflow: hidden; }
  body {
    position: relative;
    background: var(--white);
    font-family: "Open Sans", Arial, sans-serif;
    color: var(--text);
  }
  .top-bar { position: absolute; left: 0; top: 0; width: 1200px; height: 4px; background: var(--bar); }

  .site-header { position: absolute; left: 0; top: 4px; width: 1200px; height: 107px; background: var(--white); }
  .brand { position: absolute; left: 112px; top: 44px; display: flex; align-items: center; gap: 10px; }
  .brand-dot { width: 30px; height: 30px; border-radius: 50%; background: var(--olive); }
  .brand-name { font-size: 34px; font-weight: 600; color: var(--olive); letter-spacing: -0.5px; }
  .main-nav a {
    position: absolute; top: 50px; font-size: 15px; color: var(--muted); text-decoration: none;
  }

  .hero { position: absolute; left: 0; top: 111px; width: 1200px; height: 434px; overflow: hidden; }
  .hero-photo {
    position: absolute; inset: 0;
    background:
      radial-gradient(ellipse 380px 220px at 860px 230px, #e9e4ef 0%, rgba(233,228,239,0) 70%),
      radial-gradient(ellipse 260px 260px at 1080px 140px, #6b4a4d 0%, rgba(107,74,77,0) 80%),
      linear-gradient(90deg, #d9dcde 0%, #c9c3c2 45%, #a88986 75%, #8a6a6a 100%);
  }
  .hero-frame {
    position: absolute; left: 348px; top: 25px; width: 166px; height: 160px;
    border: 12px solid rgba(176,188,110,0.45); border-radius: 14px;
  }
  .hero-halo {
    position: absolute; left: 105px; top: 59px; width: 368px; height: 323px;
    background: rgba(255,255,255,0.45); border-radius: 34px 0 40px 0;
  }
  .hero-card {
    position: absolute; left: 120px; top: 78px; width: 341px; height: 287px;
    background: var(--white); border-radius: 28px 0 30px 0; padding: 16px 20px 0 20px;
  }
  .hero-title { font-size: 50px; font-weight: 400; color: var(--ink); letter-spacing: -1px; line-height: 1.2; }
  .hero-text { margin-top: 22px; font-size: 16px; line-height: 23px; color: var(--text); width: 305px; }
  .hero-actions { position: absolute; left: 12px; top: 207px; display: flex; gap: 6px; }
  .btn {
    display: block; height: 31px; line-height: 31px; text-align: center;
    font-size: 13px; font-weight: 600; color: var(--white); text-decoration: none;
  }
  .btn-signup { width: 157px; background: var(--olive-btn); }
  .btn-plans { width: 157px; background: #000; }
  .slider-dots { position: absolute; left: 268px; top: 253px; display: flex; gap: 5px; }
  .slider-dots span { width: 12px; height: 12px; border-radius: 50%; background: #333; }
  .slider-dots span.active { background: var(--olive); }

  .features { position: absolute; left: 0; top: 545px; width: 1200px; height: 225px; }
  .feature-card {
    position: absolute; left: 120px; top: 34px; width: 592px; height: 147px;
    background: linear-gradient(180deg, #f0f0f0 0%, #fafafa 100%);
    border: 1px solid #dcdcdc;
    box-shadow: 0 4px 8px rgba(0,0,0,0.12);
    padding: 10px 20px 0 50px;
  }
  .feature-arrow { position: absolute; left: 88px; top: 45px; }
  .feature-title { font-size: 20px; font-weight: 400; line-height: 26px; color: var(--olive-dark); }
  .feature-text { margin-top: 10px; font-size: 10.5px; line-height: 16px; color: var(--muted); }
  .read-more {
    position: absolute; font-size: 11.5px; color: var(--olive-dark); text-decoration: underline;
  }
  .feature-card .read-more { right: 21px; bottom: 4px; }
  .feature-plain { position: absolute; left: 747px; top: 43px; width: 345px; }
  .feature-plain .feature-title { color: #222; }
  .feature-plain .read-more { right: 24px; top: 112px; }

  .footer-shadow {
    position: absolute; left: 0; top: 770px; width: 1200px; height: 18px;
    background: linear-gradient(180deg, rgba(0,0,0,0.07), rgba(0,0,0,0));
  }
  .site-footer { position: absolute; left: 0; top: 770px; width: 1200px; height: 66px; }
  .copyright { position: absolute; left: 110px; top: 29px; font-size: 13px; color: var(--muted); }
  .social { position: absolute; left: 965px; top: 18px; display: flex; gap: 3px; }
  .social span { width: 32px; height: 32px; border-radius: 50%; background: var(--olive); }
  .social span:nth-child(2) { background: var(--olive-btn); }
  .social span:nth-child(3) { background: var(--olive-dark); }
</style>
</head>
<body>
  <div class="top-bar"></div>

  <header class="site-header">
    <div class="brand">
      <span class="brand-dot"></span>
      <span class="brand-name">Pingo.QZ</span>
    </div>
    <nav class="main-nav">
      <a href="#" style="left:778px">How It Works</a>
      <a href="#" style="left:921px">Support</a>
      <a href="#" style="left:1050px">Login</a>
    </nav>
  </header>

  <section class="hero">
    <div class="hero-photo" role="img" aria-label="Photo of hands using a tablet showing charts on a desk"></div>
    <div class="hero-frame"></div>
    <div class="hero-halo"></div>
    <div class="hero-card">
      <h1 class="hero-title">Pingo.QZ</h1>
      <p class="hero-text">Choosing and registeringa great domain name is one of the first steps towards building a successful internet presence.</p>
      <div class="hero-actions">
        <a class="btn btn-signup" href="#">GET STARTED FREE</a>
        <a class="btn btn-plans" href="#">COMPARE PLANS</a>
      </div>
      <div class="slider-dots"><span class="active"></span><span></span><span></span></div>
    </div>
  </section>

  <section class="features">
    <article class="feature-card">
      <h2 class="feature-title">Pingo.QZ with your NameHarbor domain registraton for reliable email forwarding</h2>
      <p class="feature-text">Sed ut perspiciatis unde omnis iste natus error sit voluptatem accusantium doloremque laudantium, totam rem aperiam, eaque ipsa quae ab illo inventore veritatis et quasi architecto beatae vitae dicta sunt explicabo. Nemo enim ipsam voluptatem quia voluptas sit aspernatur</p>
      <a class="read-more" href="#">Read More</a>
    </article>
    <svg class="feature-arrow" width="64" height="122" viewBox="0 0 64 122" aria-hidden="true">
      <defs>
        <linearGradient id="arrowFill" x1="0" x2="1" y1="0" y2="0">
          <stop offset="0" stop-color="var(--arrow-dark)"/>
          <stop offset="1" stop-color="var(--arrow-light)"/>
        </linearGradient>
      </defs>
      <path d="M2 100 L2 14 Q10 2 32 0 L32 18 L62 68 L32 122 L32 104 Q12 104 2 100 Z" fill="url(#arrowFill)"/>
    </svg>

    <article class="feature-plain">
      <h2 class="feature-title">Configure your SkyVeil DNS to use pingo.qz</h2>
      <p class="feature-text">Sed ut perspiciatis unde omnis iste natus error sit voluptatem accusantium doloremque laudantium, totam rem aperiam, eaque ipsa quae ab illo inventore veritatis et quasi architecto beatae vitae</p>
      <a class="read-more" href="#">Read More</a>
    </article>
  </section>

  <div class="footer-shadow"></div>
  <footer class="site-footer">
    <p class="copyright">Copyright © 2014, Pingo.QZ All Rights Reserved.</p>
    <div class="social" aria-label="Social links"><span></span><span></span><span></span></div>
  </footer>
</body>
</html>
```